Website for my law practice

I am a solo practitioner, who specializes in family law and estate planning in Massachusetts. I need to re-do my website, as it is outdated. I like the idea of a nontraditional law firm website. My website address is: doloresquintanalaw.com. I would like to retain my logo in the green color, as part of the new website. I have uploaded my logo below.

My hourly rate has changed from what is listed on my current website. My new hourly rate is $385.00. Please use this hourly rate when creating the website.

Good morning,

I have reviewed the designs submitted so far. I am happy that the "dq" logo in the green color is part of each of the designs submitted. I am also happy that the standard items seen in law firm websites, such as the scales of justice, etc. were not incorporated. Although the green logo is great, I do not think rest of the website has to have the same green color throughout. Additionally, I was hoping for something more creative, to make the website standout and not the stock web designs you see everyday. Please incorporate more unique images if you can. For example of what I mean, please look at this website: https://www.rosalindfenwicklaw.com

```html
<!DOCTYPE html>
<html lang="en">
<head>
<meta charset="utf-8">
<title>Dolores Quintana, Attorney at Law — Website Concepts</title>
<link href="https://fonts.googleapis.com/css2?family=Josefin+Sans:wght@400;600;700&family=Open+Sans:wght@400;600&display=swap" rel="stylesheet">
<style>
:root{
  --green:#3f8f2f;
  --green-dark:#2f7322;
  --green-light:#7cbf4a;
  --ink:#2b2b2b;
  --muted:#7a7a7a;
  --line:#d9d9d9;
  --bg:#ececec;
  --band:#f1f1f1;
  --white:#ffffff;
}
*{box-sizing:border-box;margin:0;padding:0}
html,body{width:900px;height:1200px;overflow:hidden}
body{background:var(--bg);font-family:"Open Sans",sans-serif;color:var(--ink);position:relative}
.page{position:absolute;top:24px;width:414px;height:1146px;background:var(--white);display:flex;flex-direction:column;box-shadow:0 2px 8px rgba(0,0,0,.12)}
.page--a{left:30px}
.page--b{left:456px}

/* header */
.site-header{height:36px;flex-shrink:0;display:flex;align-items:center;justify-content:space-between;padding-left:10px}
.brand{display:flex;align-items:center;gap:5px;font-family:"Josefin Sans",sans-serif;font-weight:600;font-size:6px;color:var(--green);line-height:1.15}
.brand-dot{display:block;width:14px;height:14px;border-radius:50%;background:var(--green);flex-shrink:0}
.main-nav{height:100%;width:62%;background:var(--green);display:flex;align-items:center;justify-content:space-around;padding:0 6px}
.main-nav span{font-size:5.5px;color:var(--white);font-weight:600}
.main-nav .is-active{background:var(--green-light);padding:4px 5px}

/* hero */
.hero{height:210px;flex-shrink:0;position:relative;overflow:hidden}
.hero-image{position:absolute;inset:0}
.page--a .hero-image{background:radial-gradient(circle at 70% 40%,#f4f8ec 0,#dfeac6 22%,#a9cc6a 55%,#5f9d2e 100%)}
.page--b .hero-image{background:linear-gradient(180deg,#4b4f6a 0%,#8a7788 30%,#e3a774 52%,#c6625a 70%,#7a8d3d 100%)}
.hero-text{position:absolute;left:24px;top:62px;color:var(--white)}
.page--b .hero-text{left:36px;top:54px}
.hero-kicker{font-family:"Josefin Sans",sans-serif;font-size:8px}
.hero-name{font-family:"Josefin Sans",sans-serif;font-weight:700;font-size:20px;line-height:1.05;letter-spacing:.5px;margin:3px 0 10px}
.btn{display:inline-block;background:var(--green);color:var(--white);font-size:5px;font-weight:600;padding:4px 9px;border-radius:2px}

/* about */
.about{height:225px;flex-shrink:0;display:flex;gap:16px;padding:22px 18px 0 22px}
.portrait{width:140px;height:165px;background:linear-gradient(180deg,#c9c9c9,#8e8e8e);border-radius:0 0 70px 70px;border-bottom:4px solid var(--green);flex-shrink:0}
.section-title{font-family:"Josefin Sans",sans-serif;font-weight:700;font-size:14px;display:flex;align-items:center;gap:5px}
.section-title .mark{width:9px;height:9px;border:1.5px solid var(--green);border-radius:50%}
.rule{width:60px;height:1.5px;background:var(--green);margin:4px 0 8px}
.about p{font-size:5px;line-height:1.7;color:var(--muted);margin-bottom:8px}

/* services */
.services{height:225px;flex-shrink:0;background:var(--band);padding-top:14px}
.services .section-title{justify-content:center}
.services .rule{margin:4px auto 12px}
.service-cards{display:flex;gap:10px;padding:0 20px}
.service-card{flex:1;border-radius:6px;overflow:hidden;background:var(--white);box-shadow:0 1px 4px rgba(0,0,0,.15)}
.service-photo{height:120px}
.service-photo--family{background:linear-gradient(135deg,#d8c7b4,#9a8a78)}
.service-photo--estate{background:linear-gradient(135deg,#9ec0d8,#6b8a5a)}
.service-label{height:26px;background:var(--green);color:var(--white);font-family:"Josefin Sans",sans-serif;font-weight:700;font-size:9px;display:flex;align-items:center;justify-content:space-between;padding:0 8px}
.service-label svg{width:12px;height:12px}

/* contact */
.contact{height:240px;flex-shrink:0;padding:22px 26px 0;text-align:center}
.contact .section-title{justify-content:center}
.contact .rule{margin:4px auto 6px}
.contact-strip{background:var(--green);color:var(--white);font-size:4.5px;padding:3px;margin-bottom:12px}
.contact-form{display:grid;grid-template-columns:1fr 1fr;gap:8px 14px;text-align:left}
.field{font-size:4.5px;color:var(--muted);border-bottom:1px solid var(--line);padding-bottom:3px}
.field--wide{grid-column:1 / 3;height:44px}
.contact-submit{margin-top:12px;text-align:right}

/* footer */
.site-footer{height:210px;flex-shrink:0;background:var(--green);color:var(--white);display:flex;flex-direction:column}
.footer-main{flex:1;display:flex;padding:26px 18px 0;gap:16px}
.footer-brand{width:110px;text-align:center;font-family:"Josefin Sans",sans-serif;font-weight:600;font-size:7px;line-height:1.3}
.footer-brand .brand-dot{width:40px;height:40px;background:var(--white);margin:0 auto 8px}
.footer-col h4{font-family:"Josefin Sans",sans-serif;font-weight:700;font-size:9px;margin-bottom:2px}
.footer-col .rule{background:var(--white);width:30px;margin:2px 0 6px}
.link-grid{display:grid;grid-template-columns:auto auto;gap:3px 14px;font-size:5px}
.signup{width:86px;height:12px;background:var(--white);border-radius:2px;display:flex;justify-content:flex-end}
.signup span{width:22px;background:var(--green-dark);border-radius:0 2px 2px 0}
.footer-bottom{height:22px;border-top:1px solid rgba(255,255,255,.3);font-size:4.5px;display:flex;align-items:center;justify-content:center}
</style>
</head>
<body>

<section class="page page--a">
  <header class="site-header">
    <div class="brand"><span class="brand-dot"></span><span>Dolores Quintana<br>Attorney at Law</span></div>
    <nav class="main-nav"><span class="is-active">Home</span><span>About</span><span>Family Law</span><span>Estate Planning</span><span>Fees</span><span>Contact</span></nav>
  </header>
  <div class="hero">
    <div class="hero-image" role="img" aria-label="Dandelion seed head against a soft green meadow"></div>
    <div class="hero-text">
      <div class="hero-kicker">Welcome to</div>
      <div class="hero-name">DOLORES<br>QUINTANA</div>
      <span class="btn">Get Started</span>
    </div>
  </div>
  <div class="about">
    <div class="portrait" role="img" aria-label="Portrait photograph of the attorney"></div>
    <div>
      <div class="section-title">ABOUT <span class="mark"></span></div>
      <div class="rule"></div>
      <p>Dolores Quintana is a solo practitioner in Massachusetts focusing on family law and estate planning. She offers clear, caring guidance through divorce, custody, wills and trusts, helping each client make steady decisions for the people who matter most.</p>
      <span class="btn">Read More</span>
    </div>
  </div>
  <div class="services">
    <div class="section-title">OUR SERVICES</div>
    <div class="rule"></div>
    <div class="service-cards">
      <div class="service-card">
        <div class="service-photo service-photo--family" role="img" aria-label="Family gathered together at home"></div>
        <div class="service-label">Family Law<svg viewBox="0 0 12 12"><circle cx="6" cy="6" r="5.5" fill="#fff"/><path d="M3.5 6h5M6.5 4l2 2-2 2" stroke="#3f8f2f" stroke-width="1.2" fill="none"/></svg></div>
      </div>
      <div class="service-card">
        <div class="service-photo service-photo--estate" role="img" aria-label="Small model house beside estate documents"></div>
        <div class="service-label">Estate Planning<svg viewBox="0 0 12 12"><circle cx="6" cy="6" r="5.5" fill="#fff"/><path d="M3.5 6h5M6.5 4l2 2-2 2" stroke="#3f8f2f" stroke-width="1.2" fill="none"/></svg></div>
      </div>
    </div>
  </div>
  <div class="contact">
    <div class="section-title">CONTACT US</div>
    <div class="rule"></div>
    <div class="contact-strip">Let's Talk About Your Consultation Needs</div>
    <div class="contact-form">
      <div class="field">Name</div><div class="field">Phone</div>
      <div class="field">Email</div><div class="field">Subject</div>
      <div class="field field--wide">Message</div>
    </div>
    <div class="contact-submit"><span class="btn">Send Now</span></div>
  </div>
  <footer class="site-footer">
    <div class="footer-main">
      <div class="footer-brand"><span class="brand-dot"></span>Dolores Quintana<br>Attorney at Law</div>
      <div class="footer-col">
        <h4>Quick Links</h4><div class="rule"></div>
        <div class="link-grid"><span>Home</span><span>Location</span><span>Family Law</span><span>Contact</span><span>Estate Planning</span><span>Blog</span><span>About</span><span>Fees</span></div>
      </div>
      <div class="footer-col">
        <h4>Keep In Touch</h4><div class="rule"></div>
        <div class="signup"><span></span></div>
      </div>
    </div>
    <div class="footer-bottom">Copyright © 2024 Dolores Quintana. All Rights Reserved</div>
  </footer>
</section>

<section class="page page--b">
  <header class="site-header">
    <div class="brand"><span class="brand-dot"></span><span>Dolores Quintana<br>Attorney at Law</span></div>
    <nav class="main-nav"><span class="is-active">Home</span><span>About</span><span>Family Law</span><span>Estate Planning</span><span>Fees</span><span>Contact</span></nav>
  </header>
  <div class="hero">
    <div class="hero-image" role="img" aria-label="Field of flowers under a warm sunset sky"></div>
    <div class="hero-text">
      <div class="hero-kicker">Welcome to</div>
      <div class="hero-name">DOLORES<br>QUINTANA</div>
      <span class="btn">Get Started</span>
    </div>
  </div>
  <div class="about">
    <div class="portrait" role="img" aria-label="Portrait photograph of the attorney"></div>
    <div>
      <div class="section-title">ABOUT <span class="mark"></span></div>
      <div class="rule"></div>
      <p>Dolores Quintana is a solo practitioner in Massachusetts focusing on family law and estate planning. She offers clear, caring guidance through divorce, custody, wills and trusts, helping each client make steady decisions for the people who matter most.</p>
      <span class="btn">Read More</span>
    </div>
  </div>
  <div class="services">
    <div class="section-title">OUR SERVICES</div>
    <div class="rule"></div>
    <div class="service-cards">
      <div class="service-card">
        <div class="service-photo service-photo--family" role="img" aria-label="Family gathered together at home"></div>
        <div class="service-label">Family Law<svg viewBox="0 0 12 12"><circle cx="6" cy="6" r="5.5" fill="#fff"/><path d="M3.5 6h5M6.5 4l2 2-2 2" stroke="#3f8f2f" stroke-width="1.2" fill="none"/></svg></div>
      </div>
      <div class="service-card">
        <div class="service-photo service-photo--estate" role="img" aria-label="Small model house beside estate documents"></div>
        <div class="service-label">Estate Planning<svg viewBox="0 0 12 12"><circle cx="6" cy="6" r="5.5" fill="#fff"/><path d="M3.5 6h5M6.5 4l2 2-2 2" stroke="#3f8f2f" stroke-width="1.2" fill="none"/></svg></div>
      </div>
    </div>
  </div>
  <div class="contact">
    <div class="section-title">CONTACT US</div>
    <div class="rule"></div>
    <div class="contact-strip">Let's Talk About Your Consultation Needs</div>
    <div class="contact-form">
      <div class="field">Name</div><div class="field">Phone</div>
      <div class="field">Email</div><div class="field">Subject</div>
      <div class="field field--wide">Message</div>
    </div>
    <div class="contact-submit"><span class="btn">Send Now</span></div>
  </div>
  <footer class="site-footer">
    <div class="footer-main">
      <div class="footer-brand"><span class="brand-dot"></span>Dolores Quintana<br>Attorney at Law</div>
      <div class="footer-col">
        <h4>Quick Links</h4><div class="rule"></div>
        <div class="link-grid"><span>Home</span><span>Location</span><span>Family Law</span><span>Contact</span><span>Estate Planning</span><span>Blog</span><span>About</span><span>Fees</span></div>
      </div>
      <div class="footer-col">
        <h4>Keep In Touch</h4><div class="rule"></div>
        <div class="signup"><span></span></div>
      </div>
    </div>
    <div class="footer-bottom">Copyright © 2024 Dolores Quintana. All Rights Reserved</div>
  </footer>
</section>

</body>
</html>
```